Brightmill Data Works

Our company is about IT hardwares and IT solutions. IT hardware such as PC, RAMS, storage and servers. IT solutions such as project management, BA. We are also selling new technology too.

Target Market(s)

Consumer, Small to Medium Business, Corporate

Requirements
Must have
• The business card must have the following:
• Name:
• Title:
• Contact Number:
• Email address:
• Website:
• Color: Must match the logo color upgrade

```html
<!DOCTYPE html>
<html lang="en">
<head>
<meta charset="utf-8">
<title>Brightmill Data Works – Business Card</title>
<link rel="stylesheet" href="https://fonts.googleapis.com/css2?family=Roboto:wght@400;500;700;900&display=swap">
<style>
  :root {
    --stage: #2b2b2b;
    --card-dark: #3a3a3b;
    --card-dark-edge: #323233;
    --card-light: #ffffff;
    --card-light-shade: #e9e9e9;
    --ink: #2f2f30;
    --ink-soft: #4a4a4a;
    --accent: #d08a22;
    --white: #f4f4f4;
  }
  * { box-sizing: border-box; margin: 0; padding: 0; }
  html, body {
    width: 1200px; height: 997px; overflow: hidden;
    background: var(--stage);
    font-family: "Roboto", Arial, sans-serif;
  }
  .canvas { position: relative; width: 1200px; height: 997px; }

  .card {
    position: absolute; width: 560px; height: 320px;
    border-radius: 16px; overflow: hidden;
    box-shadow: 0 18px 40px rgba(0,0,0,.45);
  }

  /* Front */
  .card-front {
    left: 70px; top: 120px;
    background: linear-gradient(160deg, var(--card-dark) 0%, var(--card-dark-edge) 100%);
    display: flex; align-items: center; justify-content: center;
  }
  .front-wordmark {
    font-weight: 900; color: var(--white); text-align: center;
    line-height: 1.05; letter-spacing: 1px;
  }
  .front-wordmark .line-main { display: block; font-size: 52px; }
  .front-wordmark .line-sub { display: block; font-size: 22px; letter-spacing: 12px; margin-top: 6px; }

  /* Back */
  .card-back {
    left: 570px; top: 500px;
    background: linear-gradient(135deg, var(--card-light) 0%, var(--card-light) 45%, var(--card-light-shade) 100%);
  }
  .back-wordmark {
    position: absolute; left: 120px; top: 40px;
    font-weight: 900; color: var(--ink); line-height: 1.05;
  }
  .back-wordmark .line-main { display: block; font-size: 36px; letter-spacing: .5px; }
  .back-wordmark .line-sub { display: block; font-size: 15px; letter-spacing: 9px; margin-top: 4px; padding-left: 70px; }
  .rule { position: absolute; height: 1.5px; background: var(--accent); }
  .rule-top { left: 400px; right: 30px; top: 104px; }
  .rule-name { left: 170px; right: 30px; top: 176px; }

  .person { position: absolute; left: 30px; top: 162px; }
  .person-name { font-size: 17px; font-weight: 700; color: var(--ink); }
  .person-title { font-size: 13px; color: var(--accent); margin-top: 2px; }

  .contacts { position: absolute; left: 30px; top: 214px; list-style: none; }
  .contacts li {
    display: flex; align-items: center; gap: 14px;
    font-size: 13px; color: var(--ink-soft); height: 20px;
  }
  .contacts svg { width: 12px; height: 12px; flex: none; }

  .footer-bands { position: absolute; left: 0; bottom: 0; width: 560px; height: 80px; }
  .website {
    position: absolute; right: 26px; bottom: 36px;
    font-size: 12px; font-weight: 500; color: var(--white); letter-spacing: .3px;
  }
</style>
</head>
<body>
<main class="canvas">

  <section class="card card-front" aria-label="Card front">
    <div class="front-wordmark">
      <span class="line-main">BRIGHTMILL</span>
      <span class="line-sub">DATA WORKS</span>
    </div>
  </section>

  <section class="card card-back" aria-label="Card back">
    <div class="back-wordmark">
      <span class="line-main">BRIGHTMILL</span>
      <span class="line-sub">DATA WORKS</span>
    </div>
    <div class="rule rule-top"></div>

    <div class="person">
      <p class="person-name">Elena Marwood</p>
      <p class="person-title">Director</p>
    </div>
    <div class="rule rule-name"></div>

    <ul class="contacts">
      <li>
        <svg viewBox="0 0 12 12"><circle cx="6" cy="6" r="6" fill="#d08a22"/><path d="M3.5 4.2c0 2.4 1.9 4.3 4.3 4.3l.7-1.1-1.2-.7-.6.5c-.8-.4-1.4-1-1.8-1.8l.5-.6-.7-1.2z" fill="#fff"/></svg>
        2095550148
      </li>
      <li>
        <svg viewBox="0 0 12 12"><circle cx="6" cy="6" r="6" fill="#d08a22"/><path d="M3.5 4.2c0 2.4 1.9 4.3 4.3 4.3l.7-1.1-1.2-.7-.6.5c-.8-.4-1.4-1-1.8-1.8l.5-.6-.7-1.2z" fill="#fff"/></svg>
        2045550172
      </li>
      <li>
        <svg viewBox="0 0 12 12"><circle cx="6" cy="6" r="6" fill="#d08a22"/><rect x="3" y="4" width="6" height="4.2" fill="none" stroke="#fff" stroke-width=".9"/><path d="M3 4l3 2.3L9 4" fill="none" stroke="#fff" stroke-width=".9"/></svg>
        info@brightmilldata.com
      </li>
    </ul>

    <svg class="footer-bands" viewBox="0 0 560 80" preserveAspectRatio="none" aria-hidden="true">
      <path d="M0 70 L300 62 Q310 62 312 70 L312 80 L0 80 Z" fill="#d08a22"/>
      <path d="M300 80 L312 80 L316 26 Q318 12 334 12 L560 12 L560 80 Z" fill="#3a3a3b"/>
      <path d="M0 74 L560 74 L560 80 L0 80 Z" fill="#3a3a3b" opacity=".9"/>
    </svg>
    <p class="website">www.brightmilldata.com</p>
  </section>

</main>
</body>
</html>
```